Exciting opportunity to create logo and a label for our natural health brand.

About us

We are a customer centric health supplement brand who believes in natural medicine and high quality ingredients. We take a holistic approach to healthcare, with an eastern philosophy. We believe in being partners with our customers in their health care journey and are invested in their well being.

Our brand philosophy and values are attached (see Vorna philosophy.png). Our personality traits are:

- Natural
- Fresh
- Modern
- Balanced (in a holistic sense)

Task breakdown

1. Design a fresh feeling logo for us
- We want it to represent our values and high quality ingredients. We would like the quality of the product to be reflected in the branding and have a high end feel.
- Logo text must include Vorna Health Sciences
- We want the Vorna to be the focus of the logo (see uploaded image Vorna logo example.png)
The logo does not have to follow this layout, but we just want the Vorna to stand out. Feel free to use your creative license on this!

2. Create an attractive label to go on the supplement bottle
- The designs need to be eye catching, give a sense of high end ingredients and natural products and tie in with the logo to give a joined up feel.
- We are selling our products online and need them to really stand out from the competition.
- See examples of labels and packaging we like (1 -7 label design).

The initial label we would like you to design would be for our product Calm Drift. It is a product that assists in the management of Anxiety and stress. The label will appear on the bottle that holds the capsules for this supplement, see uploaded files (Example plain bottles.png). The bottles may be white as the picture shows or dark blue recyclable plastic or dark brown glass . We don't have the exact dimensions of the bottle yet, but I will follow up with these.

The label needs to include the following things:
1. The logo
2. The name of the product
3. The product is to help with the relief of Anxiety and Stress
4. Number of capsules the bottle contains
5. The back of the label should have
i) The ingredients
ii) Dosage
iii) Directions of use

Please use placeholder text where needed.

We look forward to seeing your design. Thank you.

```html
<!DOCTYPE html>
<html lang="en">
<head>
<meta charset="utf-8">
<title>Vorna Health Sciences – Calm Drift Label</title>
<link rel="stylesheet" href="https://fonts.googleapis.com/css2?family=Barlow:wght@500;600&family=Montserrat:wght@500;800&family=Ubuntu:wght@500;700&display=swap">
<style>
  :root {
    --stage: #e4e4e4;
    --label-yellow: #fbe57a;
    --label-yellow-deep: #f3da68;
    --ink-brown: #4a3b2f;
    --leaf-green: #6ab159;
    --leaf-light: #a9d79b;
    --blossom: #ffffff;
  }
  * { margin: 0; padding: 0; box-sizing: border-box; }
  html, body {
    width: 1200px;
    height: 750px;
    overflow: hidden;
    background: var(--stage);
  }
  .canvas {
    position: relative;
    width: 1200px;
    height: 750px;
  }
  .label {
    position: absolute;
    left: 320px;
    top: 26px;
    width: 560px;
    height: 698px;
    background: linear-gradient(90deg, var(--label-yellow) 0%, var(--label-yellow) 72%, var(--label-yellow-deep) 100%);
    color: var(--ink-brown);
    overflow: hidden;
  }
  .leaf-decor {
    position: absolute;
    width: 180px;
    height: 225px;
    background: radial-gradient(ellipse at center, rgba(106, 177, 89, 0.75) 0%, rgba(169, 215, 155, 0.55) 45%, rgba(251, 229, 122, 0) 72%);
  }
  .leaf-decor--top-left { left: 10px; top: 62px; }
  .leaf-decor--top-right { right: 10px; top: 62px; }
  .leaf-decor--bottom-left { left: 10px; top: 395px; }
  .leaf-decor--bottom-right { right: 10px; top: 395px; }
  .blossom-decor {
    position: absolute;
    width: 56px;
    height: 56px;
    border-radius: 50%;
    background: radial-gradient(circle, rgba(255, 255, 255, 0.9) 0%, rgba(255, 255, 255, 0.5) 40%, rgba(255, 255, 255, 0) 70%);
  }
  .blossom-decor--upper { left: 252px; top: 176px; }
  .blossom-decor--lower { left: 252px; top: 430px; }
  .blossom-decor--left { left: 26px; top: 300px; }
  .blossom-decor--right { right: 26px; top: 300px; }
  .blossom-decor--corner-tl { left: 4px; top: 14px; width: 40px; height: 40px; }
  .blossom-decor--corner-tr { right: 4px; top: 14px; width: 40px; height: 40px; }
  .blossom-decor--corner-bl { left: 4px; top: 604px; width: 40px; height: 40px; }
  .blossom-decor--corner-br { right: 4px; top: 604px; width: 40px; height: 40px; }
  .brand {
    position: absolute;
    left: 0; right: 0;
    top: 38px;
    text-align: center;
  }
  .brand__name {
    font-family: "Barlow", sans-serif;
    font-weight: 500;
    font-size: 66px;
    line-height: 1;
    letter-spacing: 1px;
  }
  .brand__tagline {
    margin-top: 6px;
    font-family: "Barlow", sans-serif;
    font-weight: 600;
    font-size: 13px;
    letter-spacing: 4px;
  }
  .product {
    position: absolute;
    left: 0; right: 0;
    top: 308px;
    text-align: center;
  }
  .product__name {
    font-family: "Montserrat", sans-serif;
    font-weight: 800;
    font-size: 36px;
    line-height: 1;
  }
  .product__claim {
    margin-top: 4px;
    font-family: "Montserrat", sans-serif;
    font-weight: 500;
    font-size: 10.5px;
  }
  .count {
    position: absolute;
    left: 0; right: 0;
    top: 538px;
    text-align: center;
    font-family: "Ubuntu", sans-serif;
  }
  .count__number { font-weight: 700; font-size: 30px; line-height: 1; }
  .count__unit { font-weight: 500; font-size: 20px; letter-spacing: 2px; line-height: 1.2; }
  .net-weight {
    position: absolute;
    left: 0; right: 0;
    top: 643px;
    text-align: center;
    font-family: "Ubuntu", sans-serif;
    font-weight: 500;
    font-size: 27px;
    letter-spacing: 0.5px;
  }
</style>
</head>
<body>
<main class="canvas">
  <section class="label">
    <div class="leaf-decor leaf-decor--top-left" role="img" aria-label="Curving green leaf sprig"></div>
    <div class="leaf-decor leaf-decor--top-right" role="img" aria-label="Curving green leaf sprig"></div>
    <div class="leaf-decor leaf-decor--bottom-left" role="img" aria-label="Curving green leaf sprig"></div>
    <div class="leaf-decor leaf-decor--bottom-right" role="img" aria-label="Curving green leaf sprig"></div>

    <div class="blossom-decor blossom-decor--upper" role="img" aria-label="Small white flower"></div>
    <div class="blossom-decor blossom-decor--lower" role="img" aria-label="Small white flower"></div>
    <div class="blossom-decor blossom-decor--left" role="img" aria-label="Small white flower"></div>
    <div class="blossom-decor blossom-decor--right" role="img" aria-label="Small white flower"></div>
    <div class="blossom-decor blossom-decor--corner-tl" role="img" aria-label="Small white flower"></div>
    <div class="blossom-decor blossom-decor--corner-tr" role="img" aria-label="Small white flower"></div>
    <div class="blossom-decor blossom-decor--corner-bl" role="img" aria-label="Small white flower"></div>
    <div class="blossom-decor blossom-decor--corner-br" role="img" aria-label="Small white flower"></div>

    <header class="brand">
      <div class="brand__name">vorna</div>
      <div class="brand__tagline">HEALTH SCIENCE</div>
    </header>

    <div class="product">
      <h1 class="product__name">CALM DRIFT</h1>
      <p class="product__claim">REDUCE STRESS AND ANXIETY NATURALLY</p>
    </div>

    <div class="count">
      <div class="count__number">60</div>
      <div class="count__unit">CAPSULES</div>
    </div>

    <p class="net-weight">Net Wt 36g &#8494; (1.27oz)</p>
  </section>
</main>
</body>
</html>
```